BildeVOLD buisnesscard

Hey :) I need a modern buisnesscard for my company BildeVOLD
It most have:
Dagligleder og Fotograf: Henrik Audun Strandvik

Mob: +4791264085
Epost: post@bildevold.example
Adresse: Kvernbakken9, 6040 Strandvoll

Facbook and instagram logo with text BildeVOLD

BildeVOLD logo

It Company

```html
<!DOCTYPE html>
<html lang="no">
<head>
<meta charset="utf-8">
<title>BildeVOLD – visittkort</title>
<link rel="stylesheet" href="https://fonts.googleapis.com/css2?family=Khand:wght@600&family=Roboto:wght@400;500&display=swap">
<style>
  :root {
    --backdrop: #e6e6e6;
    --card-white: #f7f7f7;
    --brand-grey: #8c8c8c;
    --name-grey: #7a7a7a;
    --text-grey: #8a8a8a;
    --front-top: #bdbdbd;
    --front-bottom: #8f8f8f;
    --white: #ffffff;
  }
  * { margin: 0; padding: 0; box-sizing: border-box; }
  html, body { width: 1200px; height: 576px; overflow: hidden; background: var(--backdrop); }
  .canvas { position: relative; width: 1200px; height: 576px; font-family: "Roboto", sans-serif; }

  .card { position: absolute; border-radius: 8px; overflow: hidden; box-shadow: 0 3px 8px rgba(0,0,0,.18); }

  .card--front {
    left: 82px; top: 139px; width: 484px; height: 294px;
    background: linear-gradient(180deg, var(--front-top) 0%, #a5a5a5 55%, var(--front-bottom) 100%);
  }
  .front-wordmark {
    position: absolute; left: 0; right: 0; top: 168px;
    text-align: center; color: var(--white);
    font: 500 40px/1 "Roboto", sans-serif; letter-spacing: .5px;
  }

  .card--back { left: 602px; top: 139px; width: 482px; height: 292px; background: var(--card-white); }
  .back-waves { position: absolute; inset: 0; }
  .holder-name {
    position: absolute; left: 17px; top: 39px;
    font: 600 20px/1 "Khand", sans-serif; color: var(--name-grey);
  }
  .holder-title {
    position: absolute; left: 17px; top: 64px;
    font: 400 12px/1 "Roboto", sans-serif; color: var(--text-grey);
  }
  .back-wordmark {
    position: absolute; right: 26px; top: 110px;
    font: 500 30px/1 "Roboto", sans-serif; color: var(--brand-grey);
  }
  .contact-list { position: absolute; left: 26px; top: 150px; list-style: none; }
  .contact-item {
    display: flex; align-items: center; gap: 7px; height: 17px;
    font: 400 13px/1 "Roboto", sans-serif; color: var(--text-grey);
  }
  .contact-item svg { width: 11px; height: 11px; flex: none; }
  .contact-item--social { margin-top: 7px; }
  .social-square { width: 11px; height: 11px; background: var(--text-grey); border-radius: 2px; flex: none; }
  .website {
    position: absolute; right: 26px; top: 243px;
    font: 400 12px/1 "Roboto", sans-serif; color: var(--white);
  }
</style>
</head>
<body>
<div class="canvas">

  <section class="card card--front" aria-label="Forside">
    <p class="front-wordmark">BildeVOLD</p>
  </section>

  <section class="card card--back" aria-label="Bakside">
    <svg class="back-waves" viewBox="0 0 482 292" width="482" height="292" aria-hidden="true">
      <path fill="#8e8e8e" d="M0,256 C120,290 260,252 340,214 C400,188 450,178 482,176 L482,185 C440,188 400,200 346,224 C262,262 130,292 0,268 Z"/>
      <path fill="#8e8e8e" d="M0,282 C140,300 270,262 350,232 C410,210 450,200 482,198 L482,292 L0,292 Z"/>
    </svg>

    <h1 class="holder-name">Henrik Audun Strandvik</h1>
    <p class="holder-title">Managing Director &amp; Photographer</p>
    <p class="back-wordmark">BildeVOLD</p>

    <ul class="contact-list">
      <li class="contact-item">
        <svg viewBox="0 0 12 12"><rect x="3" y="0.5" width="6" height="11" rx="1.2" fill="none" stroke="#8a8a8a" stroke-width="1.2"/><circle cx="6" cy="9.5" r=".7" fill="#8a8a8a"/></svg>
        +4791264085
      </li>
      <li class="contact-item">
        <svg viewBox="0 0 12 12"><rect x="0.5" y="2.5" width="11" height="7.5" fill="#8a8a8a"/><path d="M0.8,2.8 L6,7 L11.2,2.8" fill="none" stroke="#f7f7f7" stroke-width="1"/></svg>
        post@bildevold.example
      </li>
      <li class="contact-item">
        <svg viewBox="0 0 12 12"><path d="M6,11.5 C3,7.8 2,6 2,4.3 A4,4 0 0 1 10,4.3 C10,6 9,7.8 6,11.5 Z" fill="#8a8a8a"/><circle cx="6" cy="4.3" r="1.5" fill="#f7f7f7"/></svg>
        Kvernbakken9, 6040 Strandvoll
      </li>
      <li class="contact-item contact-item--social">
        <span class="social-square"></span>
        /BildeVOLD
      </li>
    </ul>

    <p class="website">www.bildevold.example</p>
  </section>

</div>
</body>
</html>
```